2018 TVPAC Conference Theme Artwork

We need artwork designed around the theme of this year's human resources conference. The theme is "Celebrating 20 Years Together Towards Tomorrow". The artwork should be designed as a 4x6 postcard and will eventually be adapted/reformatted to use on the registration website, sales materials, e-newsletters, conference guide cover and signage.

Target Market(s)

Attendees are human resources professionals. Exhibitors and sponsors are companies who want to sell their products/services to human resource professionals

Colors

Designer to choose colors to be used in the design.

Requirements
Must have
• NO BORING PIXVAULT IMAGERY PLEASE.
• Theme: Celebrating 20 Years Together Towards Tomorrow
• Event: 20th Annual TVPA Conference
• Dates/Times: Tuesday, May 15, 2018, 12:30pm - 5:00pm and Wednesday, May 16, 2018 7:30am - 5:30pm
• Website: tvpaconference.example
• Location: The HALL at the Corvane Manchester
Nice to have
• Engaging, celebratory, visually attractive
Should not have
• NO BORING PIXVAULT IMAGERY.

```html
<!DOCTYPE html>
<html lang="en">
<head>
<meta charset="utf-8">
<title>20th Annual TVPA Conference</title>
<link rel="stylesheet" href="https://fonts.googleapis.com/css2?family=Cinzel:wght@400;600;700&family=Montserrat:wght@800;900&family=Open+Sans:wght@400;600&family=PT+Serif&display=swap">
<style>
  :root {
    --navy: #1d4f8f;
    --band: #1b4a88;
    --gold: #f5c519;
    --white: #ffffff;
    --photo-light: #f1f2f4;
    --photo-mid: #c9ccd3;
  }
  html, body {
    margin: 0;
    padding: 0;
    width: 1200px;
    height: 800px;
    overflow: hidden;
    background: var(--white);
  }
  .postcard {
    position: relative;
    width: 1200px;
    height: 800px;
    background: var(--white);
    overflow: hidden;
    font-family: "Cinzel", serif;
    color: var(--navy);
  }
  .team-photo {
    position: absolute;
    left: 20px;
    top: 150px;
    width: 690px;
    height: 570px;
    background: radial-gradient(ellipse at 50% 55%, var(--photo-mid) 0%, var(--photo-light) 60%, var(--white) 100%);
  }
  .org-name {
    position: absolute;
    left: 285px;
    top: 34px;
    display: flex;
    align-items: center;
    gap: 14px;
    font-weight: 700;
    font-size: 26px;
    line-height: 1.15;
    width: 320px;
  }
  .org-mark {
    flex: 0 0 auto;
    width: 46px;
    height: 46px;
    border-radius: 50%;
    background: var(--navy);
  }
  .celebrating {
    position: absolute;
    left: 700px;
    top: 10px;
    margin: 0;
    font-size: 50px;
    font-weight: 600;
    letter-spacing: 3px;
    line-height: 60px;
  }
  .anniversary {
    position: absolute;
    left: 730px;
    top: 60px;
    width: 440px;
    height: 260px;
  }
  .anniversary svg { display: block; }
  .years {
    position: absolute;
    left: 962px;
    top: 150px;
    margin: 0;
    font-size: 52px;
    font-weight: 700;
    letter-spacing: 2px;
    line-height: 60px;
  }
  .tagline {
    position: absolute;
    left: 834px;
    top: 300px;
    margin: 0;
    font-size: 50px;
    font-weight: 600;
    line-height: 58px;
    letter-spacing: 1px;
    white-space: nowrap;
  }
  .event-badge {
    position: absolute;
    left: 716px;
    top: 482px;
    width: 484px;
    height: 68px;
    box-sizing: border-box;
    background: var(--gold);
    border: 4px solid var(--navy);
    border-right: none;
    border-radius: 34px 0 0 34px;
    display: flex;
    align-items: center;
    padding-left: 34px;
    gap: 14px;
    white-space: nowrap;
  }
  .event-number {
    font-family: "Montserrat", sans-serif;
    font-weight: 900;
    font-size: 46px;
    line-height: 1;
  }
  .event-name {
    font-size: 27px;
    font-weight: 600;
    line-height: 28px;
  }
  .schedule {
    position: absolute;
    right: 34px;
    top: 562px;
    width: 400px;
    text-align: right;
  }
  .session {
    margin: 0;
    padding: 0;
  }
  .session-day {
    display: block;
    font-size: 31px;
    font-weight: 400;
    line-height: 36px;
    white-space: nowrap;
  }
  .session-time {
    display: block;
    font-family: "PT Serif", serif;
    font-size: 26px;
    line-height: 30px;
    color: #222;
  }
  .session + .session {
    border-top: 3px solid var(--navy);
    margin-top: 6px;
    padding-top: 4px;
  }
  .footer-band {
    position: absolute;
    left: 0;
    top: 740px;
    width: 1200px;
    height: 60px;
    background: var(--band);
    display: flex;
    align-items: center;
    font-family: "Open Sans", sans-serif;
    font-size: 30px;
    color: var(--white);
  }
  .footer-web {
    margin-left: 30px;
  }
  .footer-venue {
    margin-left: auto;
    margin-right: 26px;
    display: flex;
    align-items: center;
    gap: 10px;
  }
</style>
</head>
<body>
<main class="postcard">
  <div class="team-photo" role="img" aria-label="Photo of a group of business professionals in suits walking forward together"></div>

  <div class="org-name">
    <span class="org-mark"></span>
    <span>Granite Valley People Council</span>
  </div>

  <h2 class="celebrating">Celebrating</h2>

  <div class="anniversary" aria-label="20">
    <svg width="440" height="260" viewBox="0 0 440 260">
      <ellipse cx="210" cy="122" rx="96" ry="100" fill="none" stroke="var(--gold)" stroke-width="46"/>
      <text x="28" y="245" font-family="Montserrat, sans-serif" font-weight="900" font-size="290" fill="var(--navy)">2</text>
    </svg>
  </div>
  <p class="years">Years</p>

  <h1 class="tagline">Together<br>Towards<br>Tomorrow</h1>

  <div class="event-badge">
    <span class="event-number">20th</span>
    <span class="event-name">Annual TVPA<br>Conference</span>
  </div>

  <div class="schedule">
    <p class="session">
      <span class="session-day">Tuesday, May 15, 2018</span>
      <span class="session-time">12:30pm - 5:00pm</span>
    </p>
    <p class="session">
      <span class="session-day">Wednesday, May 16, 2018</span>
      <span class="session-time">7:30am - 5:30pm</span>
    </p>
  </div>

  <footer class="footer-band">
    <span class="footer-web">www.tvpaconference.example</span>
    <span class="footer-venue">
      <svg width="22" height="32" viewBox="0 0 24 34" aria-hidden="true">
        <path d="M12 0C5.4 0 0 5.2 0 11.7 0 20.5 12 34 12 34s12-13.5 12-22.3C24 5.2 18.6 0 12 0z" fill="var(--gold)"/>
        <circle cx="12" cy="11.5" r="4.5" fill="var(--band)"/>
      </svg>
      The HALL at the Corvane Manchester
    </span>
  </footer>
</main>
</body>
</html>
```